Business Card Design for Occupational Medicine Start Up Company

We need to design a professional business card. We are a healthcare company providing occupational medicine services to blue collar industries. We are professional, efficient and high quality service providers.

Target Market(s)

Blue Collar Industry: Shipbuilding, Ports, Trucking Companies; The Executives and Safety Officers for these companies

Industry/Entity Type

Healthcare

Contact Information for Business Card

Logo, Name, Title, Email, Phone

Other font styles liked:
• Please match our Brand Guide

Requirements
Must have
• Our Company Colors and Logo

```html
<!DOCTYPE html>
<html lang="en">
<head>
<meta charset="utf-8">
<title>CrewWell Clinics – Business Card</title>
<link rel="stylesheet" href="https://fonts.googleapis.com/css2?family=Montserrat:wght@300;400;600;700&display=swap">
<style>
  :root {
    --stage: #262626;
    --card: #302f86;
    --card-light: #3a3a94;
    --card-dark: #2a2979;
    --white: #ffffff;
    --soft-white: #dcdcf0;
    --blue: #3a9ad9;
    --orange: #e8a23a;
  }
  * { box-sizing: border-box; margin: 0; padding: 0; }
  html, body {
    width: 1200px; height: 1200px; overflow: hidden;
    background: var(--stage);
    font-family: "Montserrat", Arial, sans-serif;
    color: var(--white);
  }
  .stage {
    position: relative; width: 1200px; height: 1200px;
    display: flex; justify-content: center; align-items: center; gap: 80px;
  }
  .card {
    position: relative; width: 440px; height: 750px;
    border-radius: 28px; overflow: hidden;
    background: var(--card);
    box-shadow: 0 20px 50px rgba(0,0,0,0.5);
  }
  .card-texture {
    position: absolute; inset: 0;
    background:
      radial-gradient(ellipse at 20% 25%, var(--card-light) 0%, transparent 55%),
      radial-gradient(ellipse at 85% 80%, var(--card-light) 0%, transparent 50%),
      linear-gradient(160deg, var(--card) 0%, var(--card-dark) 100%);
  }
  .content { position: absolute; inset: 0; }

  .brand {
    position: absolute; left: 0; right: 0;
    display: flex; flex-direction: column; align-items: center;
  }
  .brand-dot {
    width: 92px; height: 92px; border-radius: 50%;
    background: var(--orange);
    margin-bottom: 34px;
  }
  .brand-name {
    font-weight: 600; color: var(--white);
    text-align: center; line-height: 1.15;
  }
  .brand-name .line-main { display: block; font-size: 38px; letter-spacing: 1px; }
  .brand-name .line-sub { display: block; font-size: 17px; letter-spacing: 11px; margin-top: 6px; padding-left: 11px; }

  .front .brand { top: 215px; }
  .website {
    position: absolute; left: 0; right: 0; bottom: 46px;
    text-align: center; font-size: 17px; font-weight: 400; letter-spacing: 0.5px;
  }
  .website .accent-blue { color: var(--blue); }
  .website .accent-orange { color: var(--orange); }

  .back .brand { top: 80px; }
  .back .brand-dot { width: 80px; height: 80px; margin-bottom: 26px; }
  .holder {
    position: absolute; left: 0; right: 0; top: 368px; text-align: center;
  }
  .holder-name { font-size: 28px; font-weight: 700; letter-spacing: 1px; }
  .holder-title { font-size: 16px; font-weight: 400; color: var(--soft-white); margin-top: 4px; }

  .divider {
    position: absolute; left: 60px; right: 60px; top: 466px;
    display: flex; align-items: center; gap: 10px;
  }
  .divider-line { flex: 1; height: 2px; background: var(--blue); }
  .divider-icons { display: flex; gap: 6px; }
  .divider-icons svg { width: 20px; height: 20px; display: block; }

  .contact-list {
    position: absolute; left: 0; right: 0; top: 505px;
    list-style: none; text-align: center;
    font-size: 16px; font-weight: 400; line-height: 1.55;
  }
  .address {
    position: absolute; left: 0; right: 0; top: 652px;
    text-align: center; font-style: normal; font-size: 16px; line-height: 1.5;
  }
</style>
</head>
<body>
<main class="stage">

  <section class="card front" aria-label="Business card front">
    <div class="card-texture" role="img" aria-label="Faint large brand pattern across the card background"></div>
    <div class="content">
      <div class="brand">
        <span class="brand-dot"></span>
        <p class="brand-name"><span class="line-main">CREWWELL</span><span class="line-sub">CLINICS</span></p>
      </div>
      <p class="website">www.<span class="accent-blue">crewwell</span><span class="accent-orange">clinics</span>.com</p>
    </div>
  </section>

  <section class="card back" aria-label="Business card back">
    <div class="card-texture" role="img" aria-label="Faint large brand pattern across the card background"></div>
    <div class="content">
      <div class="brand">
        <span class="brand-dot"></span>
        <p class="brand-name"><span class="line-main">CREWWELL</span><span class="line-sub">CLINICS</span></p>
      </div>

      <div class="holder">
        <p class="holder-name">DANA HARBOR</p>
        <p class="holder-title">Senior Doctor</p>
      </div>

      <div class="divider">
        <span class="divider-line"></span>
        <div class="divider-icons">
          <svg viewBox="0 0 20 20" aria-label="Phone">
            <circle cx="10" cy="10" r="9" fill="none" stroke="var(--orange)" stroke-width="1.6"/>
            <path d="M7 6 L8.6 6 L9.2 8 L8.2 8.8 Q9 10.8 11.2 11.8 L12 10.8 L14 11.4 L14 13 Q13 14 11.6 13.8 Q7 12.6 6 8 Q6 6.6 7 6 Z" fill="var(--orange)"/>
          </svg>
          <svg viewBox="0 0 20 20" aria-label="Email">
            <circle cx="10" cy="10" r="9" fill="none" stroke="var(--orange)" stroke-width="1.6"/>
            <rect x="5.5" y="7" width="9" height="6.5" fill="none" stroke="var(--orange)" stroke-width="1.3"/>
            <path d="M5.5 7 L10 10.8 L14.5 7" fill="none" stroke="var(--orange)" stroke-width="1.3"/>
          </svg>
          <svg viewBox="0 0 20 20" aria-label="Website">
            <circle cx="10" cy="10" r="9" fill="none" stroke="var(--orange)" stroke-width="1.6"/>
            <circle cx="10" cy="10" r="4.8" fill="none" stroke="var(--orange)" stroke-width="1.2"/>
            <ellipse cx="10" cy="10" rx="2" ry="4.8" fill="none" stroke="var(--orange)" stroke-width="1.1"/>
            <line x1="5.2" y1="10" x2="14.8" y2="10" stroke="var(--orange)" stroke-width="1.1"/>
          </svg>
        </div>
        <span class="divider-line"></span>
      </div>

      <ul class="contact-list">
        <li>555-014-2286</li>
        <li>hello@crewwellclinics.com</li>
        <li>www.crewwellclinics.com</li>
      </ul>

      <address class="address">48 Harbor Lane, Suite 210<br>Dockside, State 40217</address>
    </div>
  </section>

</main>
</body>
</html>
```